Business card for medical clinic

I need an upmarket, modern medical/health business card for my clinic

Contact Information for Business Card

name, address, email, qr code

```html
<!DOCTYPE html>
<html lang="en">
<head>
<meta charset="utf-8">
<title>Meridia Care Clinic – Business Card</title>
<link href="https://fonts.googleapis.com/css2?family=Cinzel:wght@500&family=Arimo:wght@400&display=swap" rel="stylesheet">
<style>
  :root {
    --backdrop: #d3d3d3;
    --card: #ffffff;
    --brand-blue: #1d629c;
    --accent-blue: #2a9fd8;
    --rule-blue: #3b8ec6;
    --ink: #2b2b2b;
    --shadow: rgba(0, 0, 0, 0.22);
  }
  * { box-sizing: border-box; margin: 0; padding: 0; }
  html, body {
    width: 1200px; height: 915px; overflow: hidden;
    background: var(--backdrop);
  }
  .canvas {
    position: relative; width: 1200px; height: 915px;
    display: flex; flex-direction: column; align-items: center; justify-content: center;
    gap: 60px;
  }
  .card {
    position: relative; width: 620px; height: 354px;
    background: var(--card); border-radius: 22px;
    box-shadow: 0 6px 14px var(--shadow);
    font-family: "Arimo", Arial, sans-serif; color: var(--ink);
  }
  .brand {
    position: absolute; display: flex; align-items: center; gap: 14px;
  }
  .brand-circle { flex: none; }
  .brand-name {
    font-family: "Cinzel", "Times New Roman", serif; font-weight: 500;
    color: var(--brand-blue); letter-spacing: 0.04em; white-space: nowrap;
  }
  .card-front .brand { left: 50%; top: 50%; transform: translate(-50%, -50%); }
  .card-front .brand-name { font-size: 30px; }

  .card-back .brand { right: 40px; top: 42px; gap: 10px; }
  .card-back .brand-name { font-size: 19px; }

  .holder { position: absolute; left: 40px; top: 150px; }
  .holder-name {
    font-family: "Cinzel", "Times New Roman", serif; font-weight: 500;
    font-size: 24px; color: var(--brand-blue); letter-spacing: 0.03em; line-height: 1;
  }
  .holder-role { font-size: 14px; margin-top: 4px; }

  .divider {
    position: absolute; left: 40px; right: 40px; top: 205px;
    height: 1px; background: var(--rule-blue);
  }
  .contacts {
    position: absolute; left: 40px; top: 225px; list-style: none;
    font-size: 14px; line-height: 26px;
  }
  .contacts li { display: flex; align-items: center; gap: 9px; }
  .contacts svg { flex: none; }
  .address {
    position: absolute; right: 40px; top: 228px; text-align: right;
    font-size: 14px; line-height: 20px;
  }
</style>
</head>
<body>
<main class="canvas">

  <section class="card card-front" aria-label="Card front">
    <div class="brand">
      <svg class="brand-circle" width="46" height="46" viewBox="0 0 46 46" aria-hidden="true">
        <circle cx="23" cy="23" r="20" fill="none" stroke="var(--brand-blue)" stroke-width="3"/>
      </svg>
      <span class="brand-name">MERIDIA CARE CLINIC</span>
    </div>
  </section>

  <section class="card card-back" aria-label="Card back">
    <div class="brand">
      <svg class="brand-circle" width="30" height="30" viewBox="0 0 30 30" aria-hidden="true">
        <circle cx="15" cy="15" r="12.5" fill="none" stroke="var(--brand-blue)" stroke-width="2.2"/>
      </svg>
      <span class="brand-name">MERIDIA CARE CLINIC</span>
    </div>

    <div class="holder">
      <p class="holder-name">DANIEL HART</p>
      <p class="holder-role">Director/Founder</p>
    </div>

    <div class="divider"></div>

    <ul class="contacts">
      <li>
        <svg width="12" height="12" viewBox="0 0 24 24" aria-hidden="true">
          <path fill="var(--accent-blue)" d="M6.6 10.8a15.1 15.1 0 0 0 6.6 6.6l2.2-2.2c.3-.3.7-.4 1-.2 1.1.4 2.3.6 3.6.6.6 0 1 .4 1 1V20c0 .6-.4 1-1 1A17 17 0 0 1 3 4c0-.6.4-1 1-1h3.5c.6 0 1 .4 1 1 0 1.3.2 2.5.6 3.6.1.3 0 .7-.2 1z"/>
        </svg>
        05310 482 7706
      </li>
      <li>
        <svg width="12" height="12" viewBox="0 0 24 24" aria-hidden="true">
          <rect x="2" y="5" width="20" height="14" rx="2" fill="var(--accent-blue)"/>
          <path d="M3 6l9 7 9-7" fill="none" stroke="#fff" stroke-width="2"/>
        </svg>
        info@meridiacareclinic.com
      </li>
      <li>
        <svg width="12" height="12" viewBox="0 0 24 24" aria-hidden="true">
          <circle cx="12" cy="12" r="10" fill="var(--accent-blue)"/>
          <path d="M2 12h20M12 2c3 3 3 17 0 20M12 2c-3 3-3 17 0 20" fill="none" stroke="#fff" stroke-width="1.5"/>
        </svg>
        www.meridiacareclinic.com
      </li>
    </ul>

    <address class="address" style="font-style: normal;">
      2870 Harbor Lane<br>
      Westfield CA 90417
    </address>
  </section>

</main>
</body>
</html>
```